Summer Sunglass offer

Need a poster design for a spring / summer campaign. We are an opticians with good footfall. The design needs to be eye catching and aimed at 40 year old plus. The offer is Up to 50% off sunglass offer, t&c apply. (I have attached our last year campaign)
Also need a 2 sided A5 leaflet design (see attached)
I've uploaded a copy of our logo

A5 leaflet should read:

Grab a bargain on two great looks this summer Upto 50% off sunglasses
Look great and stay safe in the sun this summer

We want you to look great, feel fantastic and most of all stay safe in the sun this summer. That’s why we’re offering you 50% off prescription sunglasses with every complete pair of glasses you buy this summer or 25% off for prescription sunglasses with no other purchase.
Find you new summer looks from our gorgeous collection of frames in store. It matters to us that you look great in your new glasses as much as how well you see through them, so we’ll be on hand to help you find frames that suit you best.
What new looks will you go for? Smart or sassy? Formal or Fun? Whatever you’re in the mood for, you’ll find it in our collections this summer.
Call in today to find your new looks, and remember to bring your prescription if you don’t need an eye test.

Target Market(s)

40 + year old

Industry/Entity Type

Optician

Colors

Designer to choose colors to be used in the design.

Requirements
Must have
• Images, preferably a male and Female image

```html
<!DOCTYPE html>
<html lang="en">
<head>
<meta charset="utf-8">
<title>Summer Sunglass Offer – Larkfield Eyecare Centre</title>
<link rel="stylesheet" href="https://fonts.googleapis.com/css2?family=Barlow:wght@300;400;500&family=Bebas+Neue&display=swap">
<style>
  :root {
    --white: #ffffff;
    --band-dark: #2b3f4a;
    --teal: #07816f;
    --grey-text: #5a5a5a;
    --photo-light: #efe6da;
    --photo-mid: #c9b49a;
    --photo-deep: #5c7890;
  }
  * { margin: 0; padding: 0; box-sizing: border-box; }
  html, body { width: 849px; height: 1200px; overflow: hidden; background: var(--white); }
  .poster {
    position: relative;
    width: 849px;
    height: 1200px;
    font-family: "Barlow", sans-serif;
    background: var(--white);
  }
  .hero-photo {
    position: absolute;
    left: 0; top: 0;
    width: 849px; height: 489px;
    background:
      radial-gradient(ellipse at 35% 55%, var(--photo-deep) 0%, rgba(92,120,144,0) 45%),
      linear-gradient(100deg, var(--photo-mid) 0%, var(--photo-light) 45%, #f4eee6 70%, #b9a08a 100%);
  }
  .brand-name {
    position: absolute;
    left: 0; right: 0;
    text-align: center;
    color: var(--band-dark);
    font-weight: 500;
    text-transform: uppercase;
    white-space: nowrap;
  }
  .brand-name--header {
    top: 26px;
    font-size: 13px;
    letter-spacing: 1.6px;
  }
  .brand-name--footer {
    top: 1074px;
    font-size: 29px;
    letter-spacing: 2.4px;
  }
  .headline-band {
    position: absolute;
    left: 0; top: 489px;
    width: 849px; height: 167px;
    background: var(--band-dark);
    color: var(--white);
    text-align: center;
    font-weight: 300;
    font-size: 55px;
    line-height: 63px;
    padding-top: 21px;
    letter-spacing: 0.6px;
    white-space: nowrap;
  }
  .offer-panel {
    position: absolute;
    left: 0; top: 656px;
    width: 849px; height: 334px;
    background: var(--teal);
    color: var(--white);
    text-align: center;
  }
  .offer-title {
    font-weight: 500;
    font-size: 54px;
    line-height: 62px;
    letter-spacing: 1px;
    padding-top: 34px;
  }
  .offer-discount {
    font-family: "Bebas Neue", sans-serif;
    font-size: 75px;
    line-height: 1;
    margin-top: 25px;
    letter-spacing: 0.5px;
    word-spacing: 6px;
  }
  .offer-terms {
    font-size: 15px;
    font-weight: 300;
    color: rgba(255,255,255,0.75);
    margin-top: -6px;
  }
  .location-line {
    position: absolute;
    left: 0; right: 0; top: 1133px;
    text-align: center;
    color: var(--grey-text);
    font-weight: 300;
    font-size: 20px;
    letter-spacing: 0.6px;
    text-transform: uppercase;
  }
</style>
</head>
<body>
<main class="poster">
  <div class="hero-photo" role="img" aria-label="Photo of a smiling couple in sunglasses and casual denim and white tees on a sunny city street"></div>

  <p class="brand-name brand-name--header">Larkfield Eyecare Centre</p>

  <section class="headline-band">
    <p>LOOK GREAT AND STAY SAFE</p>
    <p>IN THE SUN THIS SUMMER</p>
  </section>

  <section class="offer-panel">
    <h1 class="offer-title">SUNGLASS<br>OFFER</h1>
    <p class="offer-discount">UP TO 50% OFF</p>
    <p class="offer-terms">*t&amp;c apply</p>
  </section>

  <p class="brand-name brand-name--footer">Larkfield Eyecare Centre</p>

  <p class="location-line">Optician in Larkfield, England</p>
</main>
</body>
</html>
```